Web Design for Webdesign company 3 page PSD

Project
---------
We need a PSD Web Design to be used in a WordPress installation.
What we would like to create is a professional looking website for a web design agency. We also need you to look for suitable stock images to be placed on these pages.
We need the design for:
Homepage
Landing page
Contact page
attached in the pages file you will find a file with more in depth details how these files should be build up.
We would like to see a desktop version and a mobile version of these pages
The website should have a 1100px width.
The mobile design should have 480px width.
The homepage should have a header slider about 450px high.
The slider is preferred full width and should have some images text and a button
Objectives
-------------
The main objective for the website is to get leads from customers in the form of a request for a quotation or a call or mail me back action. The most important action for the homepage is to link and navigate to our landing pages.
What we want to tell our visitors (our main products)
-------------------------------------------------------------------
- A website with no big investment but a monthly rate
- A successful website with no worries (a complete website, seo, hosting and a service contract for future customization is included for a monthly rate)
Color Scheme
------------
Use branding colors. You can find them in the branding.pdf file.
Additional colors:
White: #ffffff
Black: #181818
Company info
--------------
We are a starting web design / marketing agency based in The Netherlands and looking for the design of our website. Our services are (custom) webdesign, website marketing or combinations of both. Our main customer group is small business owners.
We sell websites but give the option to buy it with a lease contract.
A second product is a default website with a complete service: SEO, hosting and a service contract for a monthly rate.
Content:
-----------
If not available place Lorem Ipsum text.
There will come about 400 words of text on the landing pages
Design Competition
--------------------------
Since this is a designing competition we would like to see your creativity.
What you can expect from us is a lot of feedback 7 days a week with short response time.
You can send us the first sketchy mock ups of the homepage and we will give feedback based on these design. But we like your feedback or comments as well
Read the pages file for more in depth details how the pages should be designed

Target Market(s)
Small business owners in The Netherlands
Industry/Entity Type
It Company
Number of Pages Required
3 page
Requirements
Must have
- Homepage:
- Header slider with images, some text and a link to a custom page
- The slider should have 3 designed slides
- Landings page:
- Sidebar
- Action button for a request for a quotation
- Action button for a call me back action
- Action button for an appointment
- Contact form:
- Address details
- Contact form
Nice to have
- Homepage:
- Full width slider
- Testimonial block
- Blog items
Should not have
- Flash
- A to crowded design

```html
<!DOCTYPE html>
<html lang="en">
<head>
<meta charset="utf-8">
<title>Bright Oak – Responsive Web Design</title>
<link href="https://fonts.googleapis.com/css2?family=Arimo:wght@400;700&family=Open+Sans:wght@400;600;700&display=swap" rel="stylesheet">
<style>
:root{
  --green:#4f8a72;
  --green-dark:#3f7560;
  --green-light:#8cc7a5;
  --teal:#2f6f7e;
  --ink:#181818;
  --text:#4a4a4a;
  --muted:#777;
  --white:#ffffff;
  --band:#333333;
  --footer:#353535;
  --footer-bottom:#262626;
  --grey-bg:#f1f1f1;
  --line:#dcdcdc;
}
*{box-sizing:border-box;margin:0;padding:0}
html,body{width:1200px;height:2215px;overflow:hidden}
body{position:relative;background:var(--white);font-family:"Open Sans",Arial,sans-serif;color:var(--text)}
.abs{position:absolute}
h1,h2,h3,h4{font-family:"Arimo",Arial,sans-serif;color:var(--ink)}

/* header */
.site-header{position:absolute;left:0;top:0;width:1200px;height:108px}
.brand{position:absolute;left:92px;top:30px;display:flex;align-items:center;gap:14px}
.brand-mark{width:46px;height:46px;border-radius:50%;background:var(--teal)}
.brand-name{font-family:"Arimo",Arial,sans-serif;font-weight:700;font-size:26px;color:var(--teal);letter-spacing:.5px}
.main-nav{position:absolute;top:40px;left:569px;display:flex}
.main-nav a{font-family:"Arimo",Arial,sans-serif;font-weight:700;font-size:14px;color:#3a3a3a;text-decoration:none;letter-spacing:.5px;height:30px;line-height:30px;padding:0 21px}
.main-nav a.active{background:#555;color:var(--white);border-radius:15px;padding:0 19px;margin-right:4px}

/* hero */
.hero{position:absolute;left:0;top:108px;width:1200px;height:416px;background:radial-gradient(ellipse at 50% 40%,#8fc6a6 0%,#6aa886 45%,#4f8f6e 100%)}
.hero-title{position:absolute;left:0;width:1200px;top:20px;text-align:center;font-family:"Arimo",Arial,sans-serif;font-weight:700;font-size:47px;color:var(--white);letter-spacing:1px}
.hero-sub{position:absolute;left:0;width:1200px;top:78px;text-align:center;font-family:"Arimo",Arial,sans-serif;font-weight:700;font-size:18px;color:var(--white);letter-spacing:.5px}
.hero-devices{position:absolute;left:245px;top:128px;width:612px;height:280px;border-radius:10px;background:linear-gradient(180deg,#e9eceb 0%,#b9bfbd 100%)}
.hero-arrow{position:absolute;top:165px}
.hero-btn{position:absolute;left:892px;top:336px;width:200px;height:38px;border-radius:19px;background:var(--white);font-family:"Arimo",Arial,sans-serif;font-weight:700;font-size:14px;color:var(--ink);text-align:center;line-height:38px;letter-spacing:.5px}

/* services */
.service{position:absolute;top:561px;width:314px}
.service-photo{width:314px;height:194px}
.service h3{font-family:"Open Sans",Arial,sans-serif;font-weight:600;font-size:17px;margin-top:18px;color:var(--ink)}
.service p{font-size:13.5px;line-height:22px;margin-top:8px;color:var(--text)}
.readmore{display:block;font-size:13px;color:var(--teal);margin-top:12px}

/* quote band */
.quote-band{position:absolute;left:0;top:940px;width:1200px;height:94px;background:var(--band)}
.quote-text{position:absolute;left:92px;top:18px;width:690px;font-family:"Arimo",Arial,sans-serif;font-weight:700;font-size:20.5px;line-height:28px;color:var(--white)}
.quote-btn{position:absolute;left:877px;top:18px;width:230px;height:58px;background:var(--green);border-radius:3px;font-family:"Arimo",Arial,sans-serif;font-weight:700;font-size:20px;color:var(--white);display:flex;align-items:center;justify-content:center;gap:12px;letter-spacing:.5px}

/* welcome */
.welcome-title{position:absolute;left:92px;top:1080px;font-size:25px;font-weight:700;font-family:"Arimo",Arial,sans-serif;color:var(--ink)}
.welcome-title span{color:var(--teal)}
.welcome-copy{position:absolute;left:92px;top:1126px;width:590px;font-size:13px;line-height:22.5px}
.welcome-copy p+p{margin-top:22px}
.lease-btn{position:absolute;left:92px;top:1305px;width:170px;height:40px;background:var(--green);border-radius:3px;color:var(--white);font-family:"Arimo",Arial,sans-serif;font-weight:700;font-size:14.5px;text-align:center;line-height:40px;letter-spacing:.3px}
.welcome-photo{position:absolute;left:704px;top:1088px;width:403px;height:277px;background:linear-gradient(135deg,#2c3447 0%,#5a6074 40%,#e7e5e2 75%,#f4f3f1 100%)}

/* testimonials + blog */
.grey-band{position:absolute;left:0;top:1422px;width:1200px;height:421px;background:var(--grey-bg)}
.section-title{position:absolute;font-family:"Arimo",Arial,sans-serif;font-weight:700;font-size:22px;color:var(--ink)}
.dots{position:absolute;left:525px;top:1478px;display:flex;gap:4px}
.dots i{width:9px;height:9px;border-radius:50%;background:#d2d2d2;display:block}
.dots i:first-child{background:#a8a8a8}
.testimonial-card{position:absolute;left:92px;top:1512px;width:494px;height:180px;background:var(--white);box-shadow:0 1px 3px rgba(0,0,0,.12);padding:24px 28px;font-size:13.5px;line-height:22.5px}
.testimonial-card::after{content:"";position:absolute;left:36px;bottom:-12px;border-left:12px solid transparent;border-right:12px solid transparent;border-top:12px solid var(--white)}
.avatar{position:absolute;left:92px;top:1725px;width:70px;height:70px;border:3px solid var(--white);background:linear-gradient(160deg,#c9a58a,#8a6a55);box-shadow:0 1px 2px rgba(0,0,0,.2)}
.client-name{position:absolute;left:180px;top:1738px;font-size:16px;font-weight:600;color:var(--ink)}
.client-role{position:absolute;left:180px;top:1762px;font-size:11.5px;color:var(--muted)}
.blog-item{position:absolute;left:613px;width:494px;height:110px;border-bottom:1px solid var(--line)}
.blog-item.last{border-bottom:none}
.date-badge{position:absolute;left:0;top:0;width:52px;height:64px;background:var(--white);box-shadow:0 1px 3px rgba(0,0,0,.18);text-align:center;border-radius:2px;overflow:hidden}
.date-badge .m{display:block;height:18px;line-height:18px;background:var(--green);color:var(--white);font-size:11px;font-weight:700}
.date-badge .d{display:block;font-size:20px;font-weight:700;color:var(--ink);line-height:24px}
.date-badge .y{display:block;font-size:11px;font-weight:600;color:var(--ink)}
.blog-item h4{position:absolute;left:66px;top:0;font-family:"Open Sans",Arial,sans-serif;font-weight:700;font-size:14.5px;color:var(--ink)}
.blog-item p{position:absolute;left:66px;top:24px;width:420px;font-size:12.5px;line-height:20px}
.blog-item p a{color:var(--teal);text-decoration:none}

/* footer */
.site-footer{position:absolute;left:0;top:1843px;width:1200px;height:299px;background:var(--footer);color:#cfcfcf}
.footer-title{position:absolute;top:50px;font-family:"Arimo",Arial,sans-serif;font-weight:700;font-size:15px;line-height:19px;color:var(--white);letter-spacing:.4px}
.field{position:absolute;left:92px;width:242px;height:32px;background:var(--white);border-radius:2px;font-size:12px;color:#888;line-height:32px;padding-left:10px}
.subscribe-btn{position:absolute;left:92px;top:198px;width:242px;height:32px;background:var(--green);border-radius:2px;color:var(--white);font-family:"Arimo",Arial,sans-serif;font-weight:700;font-size:13.5px;text-align:center;line-height:32px}
.quick-links{position:absolute;left:405px;top:85px;list-style:none;font-size:13px;line-height:24px}
.contact-row{position:absolute;left:613px;display:flex;gap:16px;font-size:13px;line-height:20px}
.contact-row svg{flex:none;margin-top:3px}
.social{position:absolute;left:883px;display:flex;align-items:center;gap:12px;font-size:13px}
.social i{width:26px;height:26px;border-radius:50%;border:1.5px solid #aaa;display:block}
.footer-bottom{position:absolute;left:0;top:2142px;width:1200px;height:73px;background:var(--footer-bottom);color:#bdbdbd;font-size:12.5px;text-align:center;padding-top:16px;line-height:22px}
</style>
</head>
<body>

<header class="site-header">
  <div class="brand"><span class="brand-mark"></span><span class="brand-name">BRIGHT OAK</span></div>
  <nav class="main-nav">
    <a class="active">HOME</a><a>LANDING</a><a>TESTIMONIALS</a><a>BLOG</a><a>CONTACT</a>
  </nav>
</header>

<section class="hero">
  <h1 class="hero-title">RESPONSIVE WEB DESIGN</h1>
  <div class="hero-sub">YOUR WEBSITE READABLE ON ALL DEVICES</div>
  <div class="hero-devices" role="img" aria-label="Tablet, desktop monitor and phone showing a responsive website"></div>
  <svg class="hero-arrow" style="left:88px" width="24" height="90" viewBox="0 0 24 90"><polyline points="20,2 4,45 20,88" fill="none" stroke="rgba(255,255,255,.7)" stroke-width="2"/></svg>
  <svg class="hero-arrow" style="left:1088px" width="24" height="90" viewBox="0 0 24 90"><polyline points="4,2 20,45 4,88" fill="none" stroke="rgba(255,255,255,.7)" stroke-width="2"/></svg>
  <svg class="abs" style="left:782px;top:86px" width="130" height="70" viewBox="0 0 130 70"><path d="M120 4 C128 40 90 58 10 52" fill="none" stroke="#fff" stroke-width="1.5" stroke-dasharray="3 3"/><polyline points="18,46 8,52 18,58" fill="none" stroke="#fff" stroke-width="1.5"/></svg>
  <div class="hero-btn">MORE INFORMATION</div>
</section>

<article class="service" style="left:92px">
  <div class="service-photo" role="img" aria-label="Business team meeting around a laptop" style="background:linear-gradient(135deg,#c8d4e0,#6d7f96)"></div>
  <h3>Web design</h3>
  <p>Lorem ipsum dolor sit amet, cu per augue graeco Est ut novum no augue necessitatibus nam.</p>
  <a class="readmore">Readmore »</a>
</article>
<article class="service" style="left:442px">
  <div class="service-photo" role="img" aria-label="Two colleagues working together at a desk" style="background:linear-gradient(135deg,#dfe3e8,#4b5668)"></div>
  <h3>Website Rent</h3>
  <p>Lorem ipsum dolor sit amet, cu per augue graeco Est ut novum no augue necessitatibus nam.</p>
  <a class="readmore">Readmore »</a>
</article>
<article class="service" style="left:793px">
  <div class="service-photo" role="img" aria-label="Hand touching glowing search marketing icons" style="background:linear-gradient(135deg,#0f1d2c,#2e5a73 60%,#8ab0c4)"></div>
  <h3>Seo</h3>
  <p>Lorem ipsum dolor sit amet, cu per augue graeco Est ut novum no augue necessitatibus nam.</p>
  <a class="readmore">Readmore »</a>
</article>

<section class="quote-band">
  <div class="quote-text">A handy Lorem Ipsum Generator that helps to create dummy text for all layout needs.</div>
  <div class="quote-btn">GET A QUOTE
    <svg width="28" height="28" viewBox="0 0 28 28"><circle cx="14" cy="14" r="12" fill="none" stroke="#fff" stroke-width="2.2"/><polyline points="11,8 17,14 11,20" fill="none" stroke="#fff" stroke-width="2.6"/></svg>
  </div>
</section>

<h2 class="welcome-title">WELCOME TO <span>BRIGHT OAK</span></h2>
<div class="welcome-copy">
  <p>Lorem ipsum dolor sit amet, cu per augue graeco cotidieque. Est ut novum laudem definiebas, no augue necessitatibus nam. Te erant dissentias appellantur cum, errem mentitum conceptam ad eum. Ad has meis adipisci, eu sed iracundia reprimique, eius perpetua vis te. Fuisset democritum scribentur ex est, mei ei viderer sapientem suscipiantur.</p>
  <p>Euismod appareat explicari et quo. Mei in natum errem scribentur, idque affert abhorreant et pri, ex eum torquatos adolescens. Errroribus conclusionemque eu quo. Novum putent his eu.</p>
</div>
<div class="lease-btn">LEASE CONTRACT</div>
<div class="welcome-photo" role="img" aria-label="Hand signing a contract with a pen"></div>

<section class="grey-band"></section>
<h2 class="section-title" style="left:92px;top:1468px">Client Testimonials</h2>
<div class="dots"><i></i><i></i><i></i><i></i><i></i></div>
<blockquote class="testimonial-card">“Lorem ipsum dolor sit amet, cu per augue graeco cotidieque. Est ut novum laudem definiebas, no augue necessitatibus nam. Te erant dissentias appellantur cum, errem mentitum conceptam ad eum. Ad has meis adipisci, eu sed iracundia reprimique, eius perpetua vis te. Fuisset democritum scribentur ex est, mei ei viderer sapientem suscipiantur.”</blockquote>
<div class="avatar" role="img" aria-label="Portrait of the client"></div>
<div class="client-name">Marena Voskuilen,</div>
<div class="client-role">[lorem ipsum dolor amet]</div>

<h2 class="section-title" style="left:613px;top:1466px">Latest Blog</h2>
<div class="blog-item" style="top:1512px">
  <div class="date-badge"><span class="m">FEB</span><span class="d">01</span><span class="y">2014</span></div>
  <h4>Lorem ipsum dolor sit amet...</h4>
  <p>Lorem Ipsum is simply dummy text of the printing and typesetting industry. <a>[+]</a></p>
</div>
<div class="blog-item" style="top:1622px">
  <div class="date-badge"><span class="m">FEB</span><span class="d">01</span><span class="y">2014</span></div>
  <h4>Lorem ipsum dolor sit amet...</h4>
  <p>Lorem Ipsum is simply dummy text of the printing and typesetting industry. <a>[+]</a></p>
</div>
<div class="blog-item last" style="top:1733px">
  <div class="date-badge"><span class="m">FEB</span><span class="d">01</span><span class="y">2014</span></div>
  <h4>Lorem ipsum dolor sit amet...</h4>
  <p>Lorem Ipsum is simply dummy text of the printing and typesetting industry. <a>[+]</a></p>
</div>

<footer class="site-footer">
  <div class="footer-title" style="left:92px">SUBSCRIBE TO<br>OUR NEWSLETTER</div>
  <div class="field" style="top:116px">Enter Your Name</div>
  <div class="field" style="top:157px">Enter Your Email</div>
  <div class="subscribe-btn">SUBSCRIBE</div>

  <div class="footer-title" style="left:405px">QUICK LINKS</div>
  <ul class="quick-links"><li>Home</li><li>Landing</li><li>Testimonials</li><li>Blog</li><li>Contact</li></ul>

  <div class="footer-title" style="left:613px">CONTACT INFO</div>
  <div class="contact-row" style="top:86px">
    <svg width="12" height="16" viewBox="0 0 12 16"><path d="M6 0a6 6 0 0 0-6 6c0 4.5 6 10 6 10s6-5.5 6-10a6 6 0 0 0-6-6z" fill="#aaa"/><circle cx="6" cy="6" r="2.2" fill="#353535"/></svg>
    <span>412, Harbor Lane Park,<br>veldstra suite- 730215</span>
  </div>
  <div class="contact-row" style="top:145px">
    <svg width="12" height="14" viewBox="0 0 12 14"><path d="M2 0h3l1 4-2 1.5c.8 1.8 2 3 3.6 3.8L9 7.3l3 1V12c0 1-1 2-2 2C4.5 14 0 8.5 0 2 0 1 1 0 2 0z" fill="#aaa"/></svg>
    <span>Phone: (555)214-36-7710<br>Fax: (555)214-36-7722</span>
  </div>
  <div class="contact-row" style="top:195px">
    <svg width="13" height="12" viewBox="0 0 13 12"><path d="M0 5L6.5 0 13 5v7H0z" fill="#aaa"/><polyline points="0.5,5 6.5,9 12.5,5" fill="none" stroke="#353535" stroke-width="1.2"/></svg>
    <span>Email: info@brightoak.example<br>Website:www.brightoak.example</span>
  </div>

  <div class="footer-title" style="left:883px">STAY CONNECTED</div>
  <div class="social" style="top:85px"><i></i>Follow Us On Facenote</div>
  <div class="social" style="top:132px"><i></i>Follow Us On Chirper</div>
  <div class="social" style="top:180px"><i></i>Follow Us On WorkLink</div>
</footer>

<div class="footer-bottom">© 2015 Bright Oak All Rights Reserved.<br>Terms of Use | Legal Disclaimer | Privacy Policy | References</div>

</body>
</html>
```